Business cards to launch an education platform

Hi,
I am looking at having new business cards designed.
I am a startup, developing a web platform for schools and university, the education world. It's an online assessment system.
I would like a card that looks classy, and that is using the colors and the font of my logo.

I have attached:
1) my logo
2) A business card that I have designed quickly so you can have all the information required in the card, but I really don't like it.
3) The font that I am using (Lato Regular) to design my web platform
4) Some screenshots of my web platform so you can have a look at the style that I have.

Target Market(s)

Major market: Education system: Schools and university
Minor markets: Business in general

Industry/Entity Type

Business

Contact Information for Business Card

Clara Fenwick
Director

M: 0437 518 902
E: clara.fenwick@amberLoomSystems.com.au

Requirements
Must have
• The colors of my logo

```html
<!DOCTYPE html>
<html lang="en">
<head>
<meta charset="utf-8">
<title>Amber Loom Systems – Business Cards</title>
<link href="https://fonts.googleapis.com/css2?family=Lato:wght@400;700&display=swap" rel="stylesheet">
<style>
  :root {
    --canvas: #eef1f4;
    --card-white: #ffffff;
    --cyan-light: #1ee6f7;
    --cyan-mid: #1bc6ee;
    --cyan-deep: #18a9e3;
    --brand-navy: #1d4f8f;
    --name-blue: #1f5fa8;
    --ink: #222a33;
    --icon-blue: #2468b3;
    --shadow: rgba(20, 40, 70, 0.18);
  }
  * { margin: 0; padding: 0; box-sizing: border-box; }
  html, body {
    width: 1200px; height: 900px; overflow: hidden;
    background: var(--canvas);
    font-family: "Lato", sans-serif;
  }
  .canvas { position: relative; width: 1200px; height: 900px; }

  .card {
    position: absolute;
    width: 600px; height: 360px;
    border-radius: 4px;
    box-shadow: 0 14px 34px var(--shadow);
    overflow: hidden;
  }

  /* Back of card */
  .card--back {
    left: 110px; top: 130px;
    background: radial-gradient(ellipse at 55% 55%, var(--cyan-light) 0%, var(--cyan-mid) 45%, var(--cyan-deep) 100%);
    display: flex; align-items: center; justify-content: center;
  }
  .back-name {
    color: #ffffff;
    font-weight: 400;
    font-size: 40px;
    letter-spacing: 4px;
    text-align: center;
    line-height: 1.2;
  }

  /* Front of card */
  .card--front {
    left: 490px; top: 410px;
    background: var(--card-white);
  }
  .brand {
    position: absolute; left: 56px; top: 70px;
    display: flex; align-items: center; gap: 14px;
  }
  .brand-square {
    width: 46px; height: 46px;
    flex: none;
    background: var(--brand-navy);
  }
  .brand-name {
    color: var(--brand-navy);
    font-weight: 400;
    font-size: 28px;
    letter-spacing: 2px;
    line-height: 1.15;
  }
  .person {
    position: absolute; left: 262px; top: 170px;
  }
  .person-name {
    color: var(--name-blue);
    font-weight: 700;
    font-size: 22px;
  }
  .person-role {
    color: var(--ink);
    font-size: 15px;
    margin-top: 2px;
  }
  .contact {
    position: absolute; left: 262px; top: 250px;
    width: 310px;
    list-style: none;
    color: var(--ink);
    font-size: 14px;
  }
  .contact li {
    display: flex; align-items: center; gap: 8px;
    margin-bottom: 14px;
    white-space: nowrap;
  }
  .contact svg { width: 14px; height: 14px; flex: none; fill: var(--icon-blue); }
</style>
</head>
<body>
<main class="canvas">
  <section class="card card--back" aria-label="Card back">
    <p class="back-name">AMBER LOOM<br>Systems</p>
  </section>

  <section class="card card--front" aria-label="Card front">
    <div class="brand">
      <span class="brand-square"></span>
      <p class="brand-name">AMBER LOOM<br>Systems</p>
    </div>

    <div class="person">
      <p class="person-name">Clara Fenwick</p>
      <p class="person-role">Director</p>
    </div>

    <ul class="contact">
      <li>
        <svg viewBox="0 0 24 24" aria-hidden="true"><path d="M6.6 10.8a15.1 15.1 0 0 0 6.6 6.6l2.2-2.2c.3-.3.7-.4 1-.2 1.1.4 2.3.6 3.6.6.6 0 1 .4 1 1V20c0 .6-.4 1-1 1A17 17 0 0 1 3 4c0-.6.4-1 1-1h3.5c.6 0 1 .4 1 1 0 1.3.2 2.5.6 3.6.1.3 0 .7-.2 1l-2.3 2.2z"/></svg>
        <span>0437 518 902</span>
      </li>
      <li>
        <svg viewBox="0 0 24 24" aria-hidden="true"><path d="M2 5h20v14H2z M4 7v.4l8 5.2 8-5.2V7z" fill-rule="evenodd"/></svg>
        <span>clara.fenwick@amberLoomSystems.com.au</span>
      </li>
    </ul>
  </section>
</main>
</body>
</html>
```